Wellness bold & beautiful PowerPoint Template

I will like a PowerPoint template, matching my brand, designed for my business.
- Some words that describe our brand identity are: wellness, natural, calming, simplicity, clean
- For icons, we prefer line icons.
- Website: http://www.vendrabo.com/
- PowerPoint board: https://www.pinterest.com/morelistavy/vendrabo-powerpoint/
- Branding board: https://www.pinterest.com/morelistavy/vendrabo-branding/
FYI: I am attaching a rough draft of a powerpoint presentation we are preparing
Target Market(s)
Women 23-48 interested in wellness
Industry/Entity Type
Health And Wellness
Font styles to use
Other font styles liked:
- Open Sans, Helvitica, Meddon
Requirements
Must have
- cover page, about page, author page, table of content, table format, graph format, list format, 2 column template.
Nice to have
- time line page sample

```html
<!DOCTYPE html>
<html lang="en">
<head>
<meta charset="utf-8">
<title>Circle Charts and Reports</title>
<link href="https://fonts.googleapis.com/css2?family=Open+Sans:wght@400;700&display=swap" rel="stylesheet">
<style>
  :root {
    --leaf-light: #dff2c4;
    --leaf-mid: #7fcf8a;
    --leaf-dark: #2f9a4f;
    --card: #ffffff;
    --frame: #a6a6a6;
    --ink: #1f1f1f;
    --track: #e8f6ee;
    --rule: #d9d9d9;
    --q1: #b5228f;
    --q2: #65993d;
    --q3: #b5d27a;
    --q4: #2fa6db;
  }
  * { box-sizing: border-box; margin: 0; padding: 0; }
  html, body { width: 1200px; height: 675px; overflow: hidden; }
  body { font-family: "Open Sans", Arial, sans-serif; color: var(--ink); position: relative; }

  .backdrop {
    position: absolute; inset: 0;
    background:
      radial-gradient(circle at 20% 30%, var(--leaf-mid) 0 8%, transparent 22%),
      radial-gradient(circle at 85% 70%, var(--leaf-mid) 0 8%, transparent 24%),
      radial-gradient(circle at 60% 10%, var(--leaf-dark) 0 3%, transparent 18%),
      radial-gradient(circle at 5% 85%, var(--leaf-dark) 0 4%, transparent 20%),
      linear-gradient(135deg, var(--leaf-light), #b9e3a8 50%, var(--leaf-light));
  }

  .card {
    position: absolute; left: 78px; top: 45px; width: 1044px; height: 585px;
    background: var(--card);
  }
  .frame {
    position: absolute; left: 22px; top: 21px; width: 998px; height: 542px;
    border: 3px solid var(--frame);
  }
  .title-band {
    height: 68px; background: var(--frame);
    display: flex; align-items: center; justify-content: center;
  }
  .title-band h1 {
    color: #fff; font-size: 37px; font-weight: 700; letter-spacing: 0.5px;
  }
  .intro {
    position: absolute; left: 17px; top: 88px; width: 960px;
    font-size: 16.3px; line-height: 27px;
  }
  .charts {
    position: absolute; left: 0; right: 0; top: 204px;
    display: flex; justify-content: space-between; padding: 0 13px 0 17px;
  }
  .quarter { width: 220px; text-align: center; }
  .donut { position: relative; width: 180px; height: 180px; margin: 0 auto; }
  .donut svg { display: block; }
  .donut .value {
    position: absolute; inset: 0; display: flex; align-items: center; justify-content: center;
    font-size: 49px; font-weight: 700; letter-spacing: -1px;
  }
  .quarter h2 {
    margin-top: 27px; font-size: 18px; font-weight: 700; text-transform: uppercase;
    padding-bottom: 9px; border-bottom: 1px solid var(--rule);
    width: 168px; margin-left: auto; margin-right: auto;
  }
  .quarter p { margin-top: 11px; font-size: 18.5px; line-height: 24px; }

  .q1 { color: var(--q1); } .q2 { color: var(--q2); }
  .q3 { color: var(--q3); } .q4 { color: var(--q4); }
</style>
</head>
<body>
  <div class="backdrop" role="img" aria-label="Pattern of green leaves on a pale green background"></div>

  <main class="card">
    <section class="frame">
      <header class="title-band"><h1>CIRCLE CHARTS AND REPORTS</h1></header>
      <p class="intro">Lorem ipsum dolor sit amet, consectetur adipiscing elit. Aliquam tincidunt ante nec sem congue convallis. Pellentesque vel mauris quis nisl ornare rutrum in id risus. Proin vehicula ut sem et tempus. Interdum et malesuada fames ac ante ipsum primis in faucibus. Pellentesque. Lorem ipsum.</p>

      <div class="charts">
        <article class="quarter q1">
          <div class="donut">
            <svg width="180" height="180" viewBox="0 0 180 180">
              <circle cx="90" cy="90" r="76.5" fill="none" stroke="var(--track)" stroke-width="25"/>
              <circle cx="90" cy="90" r="76.5" fill="none" stroke="var(--q1)" stroke-width="25" stroke-dasharray="240.33 480.66" transform="rotate(-90 90 90)"/>
            </svg>
            <span class="value">50%</span>
          </div>
          <h2>First Quarter</h2>
          <p>Report of every activity in this quarter.</p>
        </article>

        <article class="quarter q2">
          <div class="donut">
            <svg width="180" height="180" viewBox="0 0 180 180">
              <circle cx="90" cy="90" r="76.5" fill="none" stroke="var(--track)" stroke-width="25"/>
              <circle cx="90" cy="90" r="76.5" fill="none" stroke="var(--q2)" stroke-width="25" stroke-dasharray="336.46 480.66" transform="rotate(-90 90 90)"/>
            </svg>
            <span class="value">70%</span>
          </div>
          <h2>Second Quarter</h2>
          <p>Report of every activity in this quarter.</p>
        </article>

        <article class="quarter q3">
          <div class="donut">
            <svg width="180" height="180" viewBox="0 0 180 180">
              <circle cx="90" cy="90" r="76.5" fill="none" stroke="var(--track)" stroke-width="25"/>
              <circle cx="90" cy="90" r="76.5" fill="none" stroke="var(--q3)" stroke-width="25" stroke-dasharray="120.17 480.66" transform="rotate(-90 90 90)"/>
            </svg>
            <span class="value">25%</span>
          </div>
          <h2>Third Quarter</h2>
          <p>Report of every activity in this quarter.</p>
        </article>

        <article class="quarter q4">
          <div class="donut">
            <svg width="180" height="180" viewBox="0 0 180 180">
              <circle cx="90" cy="90" r="76.5" fill="none" stroke="var(--track)" stroke-width="25"/>
              <circle cx="90" cy="90" r="76.5" fill="none" stroke="var(--q4)" stroke-width="25" stroke-dasharray="384.53 480.66" transform="rotate(-90 90 90)"/>
            </svg>
            <span class="value">80%</span>
          </div>
          <h2>Second Quarter</h2>
          <p>Report of every activity in this quarter.</p>
        </article>
      </div>
    </section>
  </main>
</body>
</html>
```